Global (re)insurance broker needs a business card design

We need a classic business card for our company that is headquartered in SG, with offices in Malaysia and Dubai. We specialise in insurance and reinsurance broking and consultancy for our global clients.

```html
<!DOCTYPE html>
<html lang="en">
<head>
<meta charset="utf-8">
<title>Corvane Business Card</title>
<link rel="stylesheet" href="https://fonts.googleapis.com/css2?family=Montserrat:wght@400;700&family=Open+Sans:wght@400&display=swap">
<style>
  :root {
    --page-bg: #2b2b2f;
    --card-bg: #161616;
    --brand-blue: #2b4ba0;
    --brand-mint: #c3dcb6;
    --text-light: #f2f2f2;
  }
  * { margin: 0; padding: 0; box-sizing: border-box; }
  html, body {
    width: 1200px;
    height: 947px;
    overflow: hidden;
    background: var(--page-bg);
  }
  .sheet {
    width: 1200px;
    height: 947px;
    display: flex;
    flex-direction: column;
    align-items: center;
    justify-content: center;
    gap: 28px;
  }
  .card {
    position: relative;
    width: 720px;
    height: 410px;
    background: var(--card-bg);
    border-radius: 26px;
    overflow: hidden;
  }
  .wordmark {
    font-family: "Montserrat", sans-serif;
    font-weight: 700;
    color: var(--brand-mint);
    letter-spacing: 4px;
    line-height: 1;
  }
  .card-front .wordmark {
    position: absolute;
    inset: 0;
    display: flex;
    align-items: center;
    justify-content: center;
    font-size: 104px;
  }
  .card-back .wordmark {
    position: absolute;
    top: 60px;
    left: 0;
    right: 0;
    text-align: center;
    font-size: 92px;
  }
  .details {
    position: absolute;
    top: 210px;
    left: 0;
    right: 0;
    display: flex;
    justify-content: center;
    align-items: center;
    gap: 22px;
  }
  .person { text-align: right; }
  .person-name {
    font-family: "Montserrat", sans-serif;
    font-weight: 700;
    font-size: 30px;
    color: var(--brand-blue);
  }
  .person-title {
    font-family: "Montserrat", sans-serif;
    font-weight: 400;
    font-size: 19px;
    color: var(--text-light);
    margin-top: 2px;
  }
  .divider {
    width: 2px;
    height: 84px;
    background: var(--brand-blue);
  }
  .contacts { list-style: none; }
  .contact {
    display: flex;
    align-items: center;
    gap: 9px;
    font-family: "Open Sans", sans-serif;
    font-size: 17px;
    color: var(--text-light);
    line-height: 26px;
  }
  .contact svg { width: 14px; height: 14px; flex: none; }
  .address-band {
    position: absolute;
    left: 0;
    right: 0;
    bottom: 22px;
    height: 40px;
    background: var(--brand-blue);
    display: flex;
    align-items: center;
    justify-content: center;
    font-family: "Open Sans", sans-serif;
    font-size: 18px;
    color: var(--text-light);
  }
</style>
</head>
<body>
<main class="sheet">
  <section class="card card-front" aria-label="Card front">
    <div class="wordmark">CORVANE</div>
  </section>

  <section class="card card-back" aria-label="Card back">
    <div class="wordmark">CORVANE</div>
    <div class="details">
      <div class="person">
        <p class="person-name">Mara Lin</p>
        <p class="person-title">Chief Operating Officer</p>
      </div>
      <div class="divider"></div>
      <ul class="contacts">
        <li class="contact">
          <svg viewBox="0 0 16 16" aria-hidden="true"><path fill="var(--brand-blue)" d="M3.5 1.5l2.5 0 1 3.5-1.8 1.3a8 8 0 0 0 4.5 4.5L11 9l3.5 1v2.5c0 1-1 2-2 2C6.5 14.5 1.5 9.5 1.5 3.5c0-1 1-2 2-2z"/></svg>
          +65 9100 2345
        </li>
        <li class="contact">
          <svg viewBox="0 0 16 16" aria-hidden="true"><rect x="1" y="3" width="14" height="10" rx="1.5" fill="var(--brand-blue)"/><path d="M1.5 4l6.5 5 6.5-5" fill="none" stroke="var(--card-bg)" stroke-width="1.4"/></svg>
          mara@corvane.com
        </li>
        <li class="contact">
          <svg viewBox="0 0 16 16" aria-hidden="true"><circle cx="8" cy="8" r="7" fill="var(--brand-blue)"/><path d="M1 8h14M8 1c-3 3-3 11 0 14M8 1c3 3 3 11 0 14" fill="none" stroke="var(--card-bg)" stroke-width="1"/></svg>
          www.corvane.com
        </li>
      </ul>
    </div>
    <div class="address-band">24 Harbour Lane, Meridian Tower #08-04, Singapore 048500</div>
  </section>
</main>
</body>
</html>
```